Telecommunications/Power civil contractor needs business card design

Were a new telecommunications/power underground civil contractor that is looking for a new business card design. Our company colours are silver or grey and orange. Feel free to use the white background logo or the black background logo.

Target Market(s)

Local contractors, utility companies, private sector mining/energy companies, developers.

Industry/Entity Type

Telecommunications

Contact Information for Business Card

Each card will need the following info:
Persons name:
Title:
E-mail:
Phone number:
Shop Address:
Mailing Address:

Requirements
Must have
• Each card will need the following info:
• Persons name:
• Title:
• E-mail:
• Phone number:
• Shop Address:
• Mailing Address:

```html
<!DOCTYPE html>
<html lang="en">
<head>
<meta charset="utf-8">
<title>Line Run Contracting Inc – Business Card</title>
<link href="https://fonts.googleapis.com/css2?family=Open+Sans:wght@400;600;700&display=swap" rel="stylesheet">
<style>
  :root {
    --orange: #f05a22;
    --orange-light: #f36c35;
    --grey-dark: #58595b;
    --grey-mid: #8a8b8d;
    --grey-arc: #9a9a9a;
    --white: #ffffff;
    --paper: #f4f4f4;
    --stage: #e6e6e4;
  }
  * { box-sizing: border-box; margin: 0; padding: 0; }
  html, body {
    width: 1200px;
    height: 843px;
    overflow: hidden;
    background: var(--stage);
    font-family: "Open Sans", sans-serif;
  }
  .canvas {
    position: relative;
    width: 1200px;
    height: 843px;
  }
  .card {
    position: absolute;
    left: 280px;
    width: 640px;
    height: 366px;
    overflow: hidden;
    box-shadow: 0 6px 18px rgba(0,0,0,0.18);
  }
  /* Back side */
  .card-back {
    top: 38px;
    background: linear-gradient(135deg, var(--orange-light), var(--orange));
    display: flex;
    align-items: center;
    justify-content: center;
    gap: 16px;
  }
  .card-back .brand-dot {
    width: 46px;
    height: 46px;
    border: 5px solid var(--white);
    border-radius: 50%;
  }
  .card-back .brand-name {
    color: var(--white);
    font-weight: 700;
    font-size: 30px;
    letter-spacing: 1px;
  }
  /* Front side */
  .card-front {
    top: 438px;
    background: linear-gradient(90deg, var(--paper), var(--white) 60%);
  }
  .card-front .sweep {
    position: absolute;
    inset: 0;
  }
  .contact {
    position: absolute;
    left: 38px;
    top: 108px;
    color: var(--white);
    font-size: 15px;
    line-height: 1.35;
  }
  .contact .address { margin-bottom: 8px; }
  .contact-line {
    display: flex;
    align-items: center;
    gap: 9px;
  }
  .contact-line svg { width: 13px; height: 13px; flex: none; }
  .brand {
    position: absolute;
    right: 48px;
    top: 92px;
    display: flex;
    align-items: center;
    gap: 12px;
  }
  .brand .brand-dot {
    width: 40px;
    height: 40px;
    border: 5px solid var(--orange);
    border-radius: 50%;
  }
  .brand .brand-name {
    color: var(--grey-dark);
    font-weight: 700;
    font-size: 19px;
    line-height: 1.1;
    letter-spacing: 0.5px;
  }
  .person {
    position: absolute;
    right: 48px;
    bottom: 58px;
    text-align: right;
  }
  .person .name {
    color: var(--orange);
    font-weight: 600;
    font-size: 20px;
    letter-spacing: 0.5px;
  }
  .person .title {
    color: var(--grey-dark);
    font-size: 15px;
  }
</style>
</head>
<body>
<main class="canvas">

  <section class="card card-back" aria-label="Card back">
    <span class="brand-dot"></span>
    <span class="brand-name">LINE RUN CONTRACTING INC</span>
  </section>

  <section class="card card-front" aria-label="Card front">
    <svg class="sweep" viewBox="0 0 640 366" preserveAspectRatio="none" aria-hidden="true">
      <circle cx="40" cy="338" r="302" fill="var(--grey-arc)"/>
      <circle cx="28" cy="342" r="292" fill="var(--orange)"/>
    </svg>

    <div class="contact">
      <p class="address">4120 Birchwood Road<br>Fairbanks, Alaska 99701</p>
      <p class="contact-line">
        <svg viewBox="0 0 16 16" aria-hidden="true"><path fill="#fff" d="M3.6 1.2l2.3 2.6-1.3 1.7c.9 1.9 2.4 3.4 4.2 4.3l1.7-1.3 2.6 2.3-1.2 2.2C7.3 12.9 3 8.7 1.4 2.4z"/></svg>
        <span>555 014 2290</span>
      </p>
      <p class="contact-line">
        <svg viewBox="0 0 16 16" aria-hidden="true"><rect x="1" y="3" width="14" height="10" fill="#fff"/><path d="M1 3l7 5.5L15 3" fill="none" stroke="var(--orange)" stroke-width="1.4"/></svg>
        <span>office@linerun.com</span>
      </p>
      <p class="contact-line">
        <svg viewBox="0 0 16 16" aria-hidden="true"><circle cx="8" cy="8" r="6.5" fill="none" stroke="#fff" stroke-width="1.5"/><path d="M1.5 8h13M8 1.5c-3 3.5-3 9.5 0 13M8 1.5c3 3.5 3 9.5 0 13" fill="none" stroke="#fff" stroke-width="1.2"/></svg>
        <span>www.linerun.com</span>
      </p>
    </div>

    <div class="brand">
      <span class="brand-dot"></span>
      <span class="brand-name">LINE RUN<br>CONTRACTING INC</span>
    </div>

    <div class="person">
      <p class="name">DALE MERCER</p>
      <p class="title">CEO/Founder</p>
    </div>
  </section>

</main>
</body>
</html>
```